Maple n Brook - Contact/Landing Page

I need a landing page which will essentially be the page that customers will go to from the 'website' link on QTV listing. It will provide a short overview of services which need to be selectable. a little further down can capture some contact details followed by a large Submit Now button etc...

I have some icon/logo's that can be utilised at the bottom of the page as industry type references.

Target Market(s)

End of Lease Cleaning Services

Industry/Entity Type

Cleaning Service

Colors

Designer to choose colors to be used in the design.

Requirements
Must have
• As per description
Should not have
• Colours to match my website maplenbrook.com.au

```html
<!DOCTYPE html>
<html lang="en">
<head>
<meta charset="utf-8">
<title>Maple n Brook – End of Lease Cleaning &amp; Licensed Pest Control</title>
<link href="https://fonts.googleapis.com/css2?family=Roboto:wght@400;500;700&family=Roboto+Slab:wght@400;700&display=swap" rel="stylesheet">
<style>
:root{
  --hero-blue:#2d5fa8;
  --hero-glow:#3568b3;
  --curve-dark:#1b1f2b;
  --navy:#1c3660;
  --form-blue:#2189cf;
  --brand-cyan:#2aa0e0;
  --partner-band:#e0e1e9;
  --white:#ffffff;
  --card-border:#c9ccd4;
  --arrow-grey:#6a6d75;
}
*{box-sizing:border-box;margin:0;padding:0}
html,body{width:689px;height:1200px;overflow:hidden}
body{font-family:"Roboto",Arial,sans-serif;background:var(--white);position:relative;color:var(--white)}

.hero{position:absolute;left:0;top:0;width:689px;height:433px;background:radial-gradient(ellipse at 50% 28%,var(--hero-glow) 0%,var(--hero-blue) 60%)}
.brand{position:absolute;left:0;top:92px;width:689px;display:flex;justify-content:center;align-items:center;gap:12px}
.brand-mark{width:28px;height:28px;background:var(--brand-cyan)}
.brand-name{font-family:"Roboto Slab",Georgia,serif;font-weight:700;font-size:40px;color:var(--brand-cyan);letter-spacing:1px}
.tagline{position:absolute;left:0;top:246px;width:689px;display:flex;justify-content:center;align-items:center;gap:15px;font-family:"Roboto Slab",Georgia,serif;font-size:26px;color:var(--white)}
.tagline-divider{width:1.5px;height:30px;background:var(--white)}
.hero-curve{position:absolute;left:0;top:380px;width:689px;height:60px}

.services{position:absolute;left:64px;top:481px;display:flex;gap:11px}
.service-card{position:relative;width:180px;height:233px;background:var(--navy);border:1.5px solid var(--card-border);text-align:center;overflow:hidden}
.service-photo{height:120px}
.photo-cleaning{background:linear-gradient(135deg,#4d8aa6,#8b969c 55%,#5f6a70)}
.photo-carpet{background:linear-gradient(160deg,#b9b6b1,#8d8f95 60%,#c9c8c6)}
.photo-pest{background:linear-gradient(150deg,#e4e6eb,#9da6c0 50%,#cfd2d8)}
.card-curve{position:absolute;left:0;top:102px;width:180px;height:20px}
.service-title{font-family:"Roboto Slab",Georgia,serif;font-size:14.5px;margin-top:2px;letter-spacing:.2px}
.service-text{font-size:7.5px;line-height:14.3px;margin-top:3px;padding:0 14px}
.select-btn{position:absolute;left:40px;top:183px;width:98px;height:27px;border-radius:14px;background:var(--white);color:var(--navy);font-size:10.5px;font-weight:500;display:flex;align-items:center;justify-content:center;gap:6px}
.select-box{width:11px;height:11px}

.enquiry{position:absolute;left:0;top:758px;width:689px;height:255px;background:linear-gradient(120deg,#1f82c8,var(--form-blue) 50%,#2590d4)}
.field{position:absolute;left:64px;display:flex;align-items:center}
.field label{width:54px;font-size:9px}
.field span.input{width:219px;height:19px;background:var(--white);display:block}
.submit-panel{position:absolute;left:351px;top:44px;width:274px;height:88px;background:var(--white);text-align:center}
.contact-email{display:block;margin-top:14px;font-size:12.5px;color:#2383c6}
.submit-btn{display:inline-flex;align-items:center;justify-content:center;margin-top:6px;width:129px;height:34px;border-radius:17px;background:var(--navy);color:var(--white);font-weight:500;font-size:12px}

.partners{position:absolute;left:0;top:1013px;width:689px;height:150px;background:var(--partner-band)}
.partner-tile{position:absolute;top:43px;width:124px;height:64px;background:var(--white);display:flex;align-items:center;justify-content:center}
.partner-badge{width:96px;height:34px;border-radius:3px}
.arrow{position:absolute;top:66px;width:14px;height:22px}

.site-footer{position:absolute;left:0;top:1163px;width:689px;height:37px;background:var(--hero-blue);font-size:8px}
.licence{position:absolute;left:64px;top:14px;font-weight:700}
.copyright{position:absolute;left:0;width:689px;top:13px;text-align:center}
.page-code{position:absolute;right:27px;top:14px}
</style>
</head>
<body>

<header class="hero">
  <div class="brand">
    <span class="brand-mark"></span>
    <span class="brand-name">Maple n Brook</span>
  </div>
  <div class="tagline">
    <span>End of Lease Cleaning</span>
    <span class="tagline-divider"></span>
    <span>Licensed Pest Control</span>
  </div>
</header>
<svg class="hero-curve" viewBox="0 0 689 60" aria-hidden="true">
  <path d="M0 53 Q344.5 -25 689 53 L689 60 L0 60 Z" fill="var(--curve-dark)"/>
  <path d="M0 53 Q344.5 19 689 53 L689 60 L0 60 Z" fill="var(--white)"/>
</svg>

<section class="services">
  <article class="service-card">
    <div class="service-photo photo-cleaning" role="img" aria-label="Gloved hands wiping a benchtop with a spray bottle"></div>
    <svg class="card-curve" viewBox="0 0 180 20" preserveAspectRatio="none" aria-hidden="true"><path d="M0 16 Q90 -12 180 16 L180 20 L0 20 Z" fill="var(--navy)"/></svg>
    <h2 class="service-title">CLEANING</h2>
    <p class="service-text">All interior cleaning carried out to Property Management requirements.</p>
    <div class="select-btn">SELECT
      <svg class="select-box" viewBox="0 0 11 11"><rect x=".5" y=".5" width="10" height="10" rx="1" fill="none" stroke="var(--navy)"/><path d="M2.5 5.5 L4.6 7.6 L8.6 3" fill="none" stroke="var(--navy)"/></svg>
    </div>
  </article>
  <article class="service-card">
    <div class="service-photo photo-carpet" role="img" aria-label="Carpet steam cleaning wand and machine on a lounge carpet"></div>
    <svg class="card-curve" viewBox="0 0 180 20" preserveAspectRatio="none" aria-hidden="true"><path d="M0 16 Q90 -12 180 16 L180 20 L0 20 Z" fill="var(--navy)"/></svg>
    <h2 class="service-title">CARPET CLEANING</h2>
    <p class="service-text">Carpet Steam Cleaning to Australian Standard As 3733: 1995</p>
    <div class="select-btn">SELECT
      <svg class="select-box" viewBox="0 0 11 11"><rect x=".5" y=".5" width="10" height="10" rx="1" fill="none" stroke="var(--navy)"/></svg>
    </div>
  </article>
  <article class="service-card">
    <div class="service-photo photo-pest" role="img" aria-label="Technician in protective suit spraying a kitchen"></div>
    <svg class="card-curve" viewBox="0 0 180 20" preserveAspectRatio="none" aria-hidden="true"><path d="M0 16 Q90 -12 180 16 L180 20 L0 20 Z" fill="var(--navy)"/></svg>
    <h2 class="service-title">PEST CONTROL</h2>
    <p class="service-text">Mandatory requirement for Pets on Premises</p>
    <div class="select-btn">SELECT
      <svg class="select-box" viewBox="0 0 11 11"><rect x=".5" y=".5" width="10" height="10" rx="1" fill="none" stroke="var(--navy)"/></svg>
    </div>
  </article>
</section>

<section class="enquiry">
  <div class="field" style="top:44px"><label>First Name:</label><span class="input"></span></div>
  <div class="field" style="top:79px"><label>Surname:</label><span class="input"></span></div>
  <div class="field" style="top:113px"><label>Email:</label><span class="input"></span></div>
  <div class="field" style="top:147px"><label>Phone:</label><span class="input"></span></div>
  <div class="field" style="top:182px"><label>Suburb:</label><span class="input"></span></div>
  <div class="submit-panel">
    <span class="contact-email">info@maplenbrook.com.au</span>
    <span class="submit-btn">SUBMIT NOW</span>
  </div>
</section>

<section class="partners">
  <svg class="arrow" style="left:47px" viewBox="0 0 14 22" aria-hidden="true"><path d="M12 1 L2 11 L12 21" fill="none" stroke="var(--arrow-grey)" stroke-width="1.5"/></svg>
  <div class="partner-tile" style="left:83px"><span class="partner-badge" style="background:#1b1b1b"></span></div>
  <div class="partner-tile" style="left:216px"><span class="partner-badge" style="background:#3b3f8f"></span></div>
  <div class="partner-tile" style="left:349px"><span class="partner-badge" style="background:#1f2f7a;width:64px"></span></div>
  <div class="partner-tile" style="left:482px"><span class="partner-badge" style="background:#7cb342"></span></div>
  <svg class="arrow" style="left:633px" viewBox="0 0 14 22" aria-hidden="true"><path d="M2 1 L12 11 L2 21" fill="none" stroke="var(--arrow-grey)" stroke-width="1.5"/></svg>
</section>

<footer class="site-footer">
  <span class="licence">PEST LICENCE: 5140386</span>
  <span class="copyright">Copyrights © 2021 Maple n Brook. All rights reserved.</span>
  <span class="page-code">C16</span>
</footer>

</body>
</html>
```